Harwick + Pell Architect Marketing campaign for a morern fresh architecture cutting egde firm th...

To create en exciting template for our monthly newsletters to go out to all our clients via email. I have added a bit of an idea of what we like but not limited to..... we like a nice clean fresh look with lots of white space. I hve aslo added a sketch of the type of how we might layt it out - you may have a better idea. also the pics of the projects for the first issue (issue #1)We like the opening page like the attached brewlane had and replace the cup with apic of our building/office. Cant wait to see what you come up with.

Target Market(s)

young professionals

Industry/Entity Type

Architectural

Font styles to use
Serif

Colors

Designer to choose colors to be used in the design.

Requirements
Must have
• Logo, text information provided, photos provided
Nice to have
• lots of white space, clean and frest looking

```html
<!DOCTYPE html>
<html lang="en">
<head>
<meta charset="utf-8">
<title>Harwick + Pell Architecture – Newsletter</title>
<link rel="stylesheet" href="https://fonts.googleapis.com/css2?family=Lato:wght@400;700;900&family=Open+Sans:wght@400;600;700&display=swap">
<style>
  :root {
    --ink: #1a1a1a;
    --white: #ffffff;
    --muted: #9a9a9a;
    --panel: #f2f2f2;
    --overlay: rgba(20, 20, 20, 0.72);
    --rule: #cfcfcf;
    --badge: #d6d6d6;
  }
  * { box-sizing: border-box; margin: 0; padding: 0; }
  html, body { width: 744px; height: 1200px; overflow: hidden; background: var(--white); }
  body { font-family: "Open Sans", Arial, sans-serif; color: var(--ink); position: relative; }

  .topbar { position: absolute; top: 14px; right: 30px; font-size: 10px; color: var(--muted); }

  .brand { position: absolute; top: 52px; left: 0; width: 744px; text-align: center; }
  .brand-mark { width: 92px; height: 92px; border: 9px solid var(--ink); margin: 0 auto 10px; }
  .brand-name { font-family: "Lato", Arial, sans-serif; font-weight: 700; font-size: 11px; letter-spacing: 2.5px; color: var(--ink); }

  .hero { position: absolute; top: 193px; left: 20px; width: 704px; height: 587px; overflow: hidden; }
  .hero-photo { position: absolute; inset: 0;
    background: linear-gradient(100deg, #5d7a55 0%, #6f8fb8 28%, #8aa9d4 40%, #5b4038 52%, #4a332d 75%, #3c2a25 100%); }
  .hero-rule { position: absolute; left: 0; right: 0; top: 478px; height: 2px; background: rgba(255,255,255,0.8); }
  .hero-card { position: absolute; left: 0; top: 128px; width: 364px; height: 310px; background: var(--overlay); padding: 44px 28px 0 28px; color: var(--white); }
  .hero-title { font-family: "Lato", Arial, sans-serif; font-weight: 900; font-size: 36px; line-height: 1.12; letter-spacing: 0.5px; }
  .hero-text { margin-top: 18px; font-size: 14px; line-height: 1.6; }

  .experience { position: absolute; top: 787px; left: 20px; width: 704px; height: 264px; background: var(--panel); }
  .experience-title { text-align: center; margin-top: 26px; font-size: 25px; font-weight: 400; }
  .features { display: flex; justify-content: space-around; margin-top: 26px; padding: 0 24px; }
  .feature { width: 190px; text-align: center; }
  .feature-icon { width: 62px; height: 62px; border-radius: 50%; background: var(--ink); margin: 0 auto 14px; display: flex; align-items: center; justify-content: center; }
  .feature-title { font-weight: 700; font-size: 17px; margin-bottom: 4px; }
  .feature-text { font-size: 12.5px; line-height: 1.4; }

  .footer { position: absolute; top: 1068px; left: 20px; width: 704px; height: 106px; border: 2px solid var(--rule); display: flex; align-items: center; padding: 0 22px; }
  .footer-label { font-family: "Lato", Arial, sans-serif; font-weight: 700; font-size: 13px; line-height: 1.3; letter-spacing: 0.8px; }
  .social { display: flex; gap: 14px; margin-left: 20px; }
  .social-link { font-size: 12px; font-weight: 600; color: var(--ink); }
  .divider { width: 1px; height: 70px; background: var(--rule); margin: 0 20px; }
  .badges { display: flex; gap: 22px; margin-left: 22px; align-items: center; }
  .badge { width: 72px; height: 44px; background: var(--badge); }
  .badge-round { width: 52px; height: 52px; border-radius: 50%; background: var(--badge); }
</style>
</head>
<body>
  <div class="topbar">View Browser</div>

  <header class="brand">
    <div class="brand-mark"></div>
    <div class="brand-name">HARWICK + PELL ARCHITECTURE</div>
  </header>

  <section class="hero">
    <div class="hero-photo" role="img" aria-label="Photograph of the studio building with timber cladding, trees and blue sky"></div>
    <div class="hero-rule"></div>
    <div class="hero-card">
      <h1 class="hero-title">WE’RE GLAD<br>YOU’RE HERE</h1>
      <p class="hero-text">Now that you are a Harwick + Pell Architecture insider you’ll be among the first to hear about upcoming projects that the studio is working on, completed projects, news and more.</p>
    </div>
  </section>

  <section class="experience">
    <h2 class="experience-title">Make the most &nbsp;of your experience</h2>
    <div class="features">
      <div class="feature">
        <div class="feature-icon">
          <svg width="26" height="26" viewBox="0 0 26 26"><g fill="#fff"><circle cx="13" cy="13" r="5"/><rect x="11.5" y="1" width="3" height="24" rx="1.5"/><rect x="1" y="11.5" width="24" height="3" rx="1.5"/><rect x="11.5" y="1" width="3" height="24" rx="1.5" transform="rotate(45 13 13)"/><rect x="11.5" y="1" width="3" height="24" rx="1.5" transform="rotate(-45 13 13)"/></g><circle cx="13" cy="13" r="2.2" fill="#1a1a1a"/></svg>
        </div>
        <div class="feature-title">Icon Text here</div>
        <p class="feature-text">Lorem ipsum dolor sit amet, sed do eiusmod tempor incididunt quis nostrud exercitation</p>
      </div>
      <div class="feature">
        <div class="feature-icon">
          <svg width="26" height="26" viewBox="0 0 26 26"><g fill="#fff"><circle cx="13" cy="13" r="5"/><rect x="11.5" y="1" width="3" height="24" rx="1.5"/><rect x="1" y="11.5" width="24" height="3" rx="1.5"/><rect x="11.5" y="1" width="3" height="24" rx="1.5" transform="rotate(45 13 13)"/><rect x="11.5" y="1" width="3" height="24" rx="1.5" transform="rotate(-45 13 13)"/></g><circle cx="13" cy="13" r="2.2" fill="#1a1a1a"/></svg>
        </div>
        <div class="feature-title">Icon text here</div>
        <p class="feature-text">Lorem ipsum dolor sit amet, sed do eiusmod tempor incididunt quis nostrud exercitation</p>
      </div>
      <div class="feature">
        <div class="feature-icon">
          <svg width="26" height="26" viewBox="0 0 26 26"><g fill="#fff"><circle cx="13" cy="13" r="5"/><rect x="11.5" y="1" width="3" height="24" rx="1.5"/><rect x="1" y="11.5" width="24" height="3" rx="1.5"/><rect x="11.5" y="1" width="3" height="24" rx="1.5" transform="rotate(45 13 13)"/><rect x="11.5" y="1" width="3" height="24" rx="1.5" transform="rotate(-45 13 13)"/></g><circle cx="13" cy="13" r="2.2" fill="#1a1a1a"/></svg>
        </div>
        <div class="feature-title">Icon text here</div>
        <p class="feature-text">Lorem ipsum dolor sit amet, sed do eiusmod tempor incididunt quis nostrud exercitation</p>
      </div>
    </div>
  </section>

  <footer class="footer">
    <div class="footer-label">STAY<br>CONNECTED<br>WITH US</div>
    <div class="social">
      <span class="social-link">Pixly</span>
      <span class="social-link">Friendbook</span>
      <span class="social-link">Homefeed</span>
    </div>
    <div class="divider"></div>
    <div class="footer-label">PROFESSIONAL<br>MEMBERSHIP</div>
    <div class="badges">
      <div class="badge-round" role="img" aria-label="Professional association membership badge"></div>
      <div class="badge" role="img" aria-label="Design association membership badge"></div>
    </div>
  </footer>
</body>
</html>
```